Design a business card
Business name: Harbourline Growth Advisory
Improving Business Profitibility

- An Overview of the Business & Service:

Business Performance Consulting

- The Target Market: Small to medium-sized business

- Design Specifics:
White card, blue ink, moon eclipse

No Logo

Target Market(s)

Small to medium-sized business

Font styles to use
Sans Serif

```html
<!DOCTYPE html>
<html lang="en">
<head>
<meta charset="utf-8">
<title>Harbourline Growth Advisory – Business Card</title>
<link rel="stylesheet" href="https://fonts.googleapis.com/css2?family=Open+Sans:wght@700&family=Arimo:wght@400&display=swap">
<style>
  :root {
    --backdrop: #2b2b2d;
    --card: #0d0d0e;
    --card-edge: #1a1a1c;
    --brand-blue: #3a76c2;
    --ink-white: #f2f2f2;
    --divider: #5a5a5e;
  }
  * { margin: 0; padding: 0; box-sizing: border-box; }
  html, body {
    width: 1200px; height: 900px; overflow: hidden;
    background: var(--backdrop);
  }
  .canvas { position: relative; width: 1200px; height: 900px; }
  .card {
    position: absolute; left: 300px; width: 600px; height: 343px;
    background: linear-gradient(160deg, var(--card-edge) 0%, var(--card) 60%);
    overflow: hidden;
  }
  .card::after {
    content: ""; position: absolute; left: 0; right: 0; bottom: 0;
    height: 10px; background: var(--brand-blue);
  }
  .card--front { top: 80px; }
  .card--back { top: 470px; }

  /* Front */
  .company-name {
    position: absolute; left: 0; right: 0; top: 112px;
    text-align: center; color: var(--brand-blue);
    font-family: "Open Sans", sans-serif; font-weight: 700;
    font-size: 30px; line-height: 1.2;
  }
  .tagline {
    position: absolute; left: 0; right: 0; top: 248px;
    text-align: center; color: var(--ink-white);
    font-family: "Open Sans", sans-serif; font-weight: 700;
    font-size: 17px; text-transform: uppercase; letter-spacing: 0.3px;
  }

  /* Back */
  .person { position: absolute; right: 320px; top: 110px; text-align: right; }
  .person__name {
    color: var(--brand-blue); font-family: "Open Sans", sans-serif;
    font-weight: 700; font-size: 19px; text-transform: uppercase; letter-spacing: 0.5px;
  }
  .person__role {
    color: var(--ink-white); font-family: "Arimo", sans-serif;
    font-size: 16px; margin-top: 2px;
  }
  .divider {
    position: absolute; left: 300px; top: 100px;
    width: 1px; height: 110px; background: var(--divider);
  }
  .contact {
    position: absolute; left: 322px; top: 100px; list-style: none;
    color: var(--ink-white); font-family: "Arimo", sans-serif; font-size: 16px;
  }
  .contact__item { display: flex; align-items: center; gap: 9px; height: 27px; }
  .contact__icon { width: 13px; height: 13px; fill: var(--ink-white); flex: none; }
  .address {
    position: absolute; left: 70px; top: 262px;
    color: var(--ink-white); font-family: "Arimo", sans-serif; font-size: 16px;
  }
</style>
</head>
<body>
<main class="canvas">

  <section class="card card--front" aria-label="Card front">
    <p class="company-name">Harbourline Growth<br>Advisory</p>
    <p class="tagline">Improving Business Profitibility</p>
  </section>

  <section class="card card--back" aria-label="Card back">
    <div class="person">
      <p class="person__name">Desmond Akerly</p>
      <p class="person__role">Managing Director</p>
    </div>
    <span class="divider"></span>
    <ul class="contact">
      <li class="contact__item">
        <svg class="contact__icon" viewBox="0 0 16 16" aria-hidden="true"><path d="M2 6c0-2 2.5-3 6-3s6 1 6 3l-3 1-1-2H6L5 7 2 6zm2 2h8l2 5H2l2-5zm4 1.5a2 2 0 1 0 0 4 2 2 0 0 0 0-4z"/></svg>
        <span>044-555 210 384</span>
      </li>
      <li class="contact__item">
        <svg class="contact__icon" viewBox="0 0 16 16" aria-hidden="true"><path d="M4 0h8v16H4V0zm1.5 2v10h5V2h-5zM8 13a1 1 0 1 0 0 2 1 1 0 0 0 0-2z"/></svg>
        <span>044-555 210 384</span>
      </li>
      <li class="contact__item">
        <svg class="contact__icon" viewBox="0 0 16 16" aria-hidden="true"><path d="M0 3h16v10H0V3zm1.5 1.5L8 9l6.5-4.5z" fill-rule="evenodd"/></svg>
        <span>info@harbourline.com</span>
      </li>
      <li class="contact__item">
        <svg class="contact__icon" viewBox="0 0 16 16" aria-hidden="true"><circle cx="8" cy="8" r="7.5"/><path d="M1 8h14M8 1c-3 3-3 11 0 14M8 1c3 3 3 11 0 14" stroke="#0d0d0e" stroke-width="1.2" fill="none"/></svg>
        <span>www.harbourlinegrowth.com</span>
      </li>
    </ul>
    <p class="address">48, Quayside Row Port Ellery Westmark, 204518.</p>
  </section>

</main>
</body>
</html>
```